Church needs a street sign design

We're a small church located in Silicon Valley, California. Our website is https://www.vgtmarlowfield.org/ and our address is 4817 Ferrow Ave, San Jose, California, 95873. You can look up our location on Google Maps to see the sign from Street View. I have uploaded an image of the street sign as well. The marquee, the top section of the sign, and the separating line between them both will be removed. We're seeking a design for a new backlit acrylic insert that will go on the front of the light box and the back of the lightbox. The acrylic sign will fill the entire external frame. In the future, we may build a decorative wood frame around the structural legs, as visualized in one of the uploaded files. The church's brand colors are: #003366 (dark blue), #ff6600 (vibrant orange), #228b22 (forest green). I have also uploaded the church's logo assets. Our primary font is Montserrat and the secondary is Poppins. You can deviate from these colors/fonts if the sign is still coherent with the rest of our branding. Our branding values are mission, truth, passion, and community (please do not put those words on the sign! They are just intended to guide the look of the design). The sign dimensions are 96" by 47.5". Keep in mind that the sign will be backlit on a busy street side. It will also be positioned next to an old-looking church building. We do NOT want a sign that looks traditional, old, or antiquated. Instead, we want a modern-looking sign that pairs well with our old building while helping it look more modern too. We would also like the web address clearly visible on the sign: vgtmarlowfield.org. If you have any questions, just let me know!

```html
<!DOCTYPE html>
<html lang="en">
<head>
<meta charset="utf-8">
<title>Valley Grace Tabernacle – Street Sign</title>
<link rel="stylesheet" href="https://fonts.googleapis.com/css2?family=Montserrat:wght@600;800&family=Poppins:wght@500&display=swap">
<style>
  :root {
    --navy: #0d2a5e;
    --orange: #ff6600;
    --green: #228b22;
    --white: #ffffff;
    --backdrop: #e9ebef;
  }
  * { margin: 0; padding: 0; box-sizing: border-box; }
  html, body {
    width: 1200px;
    height: 2560px;
    overflow: hidden;
    background: var(--backdrop);
  }
  .sign {
    position: absolute;
    left: 40px;
    top: 1003px;
    width: 1120px;
    height: 554px;
    background: var(--navy);
    overflow: hidden;
  }
  .name-band {
    position: absolute;
    left: 400px;
    top: 140px;
    width: 680px;
    height: 160px;
    background: var(--white);
    display: flex;
    flex-direction: column;
    justify-content: center;
    padding-left: 36px;
    color: var(--navy);
    font-family: "Montserrat", sans-serif;
  }
  .name-main {
    font-weight: 800;
    font-size: 70px;
    line-height: 1;
    letter-spacing: 1px;
  }
  .name-sub {
    font-weight: 600;
    font-size: 34px;
    line-height: 1.2;
    letter-spacing: 2px;
    margin-top: 6px;
  }
  .mark {
    position: absolute;
    left: 40px;
    top: 90px;
    width: 330px;
    height: 330px;
    display: flex;
    align-items: center;
    justify-content: center;
    color: var(--white);
    font-family: "Montserrat", sans-serif;
    font-weight: 800;
    font-size: 130px;
    letter-spacing: 4px;
  }
  .address-pill {
    position: absolute;
    left: 470px;
    top: 328px;
    width: 600px;
    height: 110px;
    border-radius: 55px;
    background: var(--green);
    color: var(--white);
    font-family: "Poppins", sans-serif;
    font-weight: 500;
    font-size: 33px;
    line-height: 1.25;
    display: flex;
    flex-direction: column;
    justify-content: center;
    align-items: center;
    text-align: center;
  }
  .divider {
    position: absolute;
    left: 0;
    top: 478px;
    width: 100%;
    height: 6px;
    background: var(--white);
  }
  .web-band {
    position: absolute;
    left: 0;
    top: 484px;
    width: 100%;
    height: 70px;
    background: var(--orange);
    color: var(--white);
    font-family: "Montserrat", sans-serif;
    font-weight: 600;
    font-size: 30px;
    letter-spacing: 14px;
    display: flex;
    align-items: center;
    justify-content: center;
  }
</style>
</head>
<body>
  <div class="sign">
    <div class="name-band">
      <div class="name-main">VALLEY GRACE</div>
      <div class="name-sub">TABERNACLE</div>
    </div>
    <div class="mark">VGT</div>
    <div class="address-pill">
      <span>4817 Ferrow Ave, San Jose</span>
      <span>California, 95873</span>
    </div>
    <div class="divider"></div>
    <div class="web-band">WWW.VGTMARLOWFIELD.ORG</div>
  </div>
</body>
</html>
```